BUSINESS CARD DESIGN

NAME- DALE VORSKIN
PHONE NUMER - 555- 714-9082
EMAIL- OFFICE@TRV-GROUNDMAKRZ.COM
BACK OF CARD- SPEACIALIZES IN LAND CLEARING, FORESTRY MUCLHING AND EXCAVATION

Contact Information for Business Card

NAME- DALE VORSKIN PHONE NUMER - 555- 714-9082 EMAIL- OFFICE@TRV-GROUNDMAKRZ.COM BACK OF CARD- SPEACIALIZES IN LAND CLEARING , MUCLHING AND EXCAVATION

```html
<!DOCTYPE html>
<html lang="en">
<head>
<meta charset="utf-8">
<title>Traverse Groundmakrz LLC – Business Card</title>
<link href="https://fonts.googleapis.com/css2?family=Roboto:wght@400;700&display=swap" rel="stylesheet">
<style>
  :root {
    --page-bg: #e4e8ea;
    --brand-green: #7fb642;
    --brand-green-deep: #6a9e33;
    --card-dark: #202125;
    --card-dark-tone: #1a1b1e;
    --text-light: #f4f6f2;
  }
  * { box-sizing: border-box; margin: 0; padding: 0; }
  html, body {
    width: 1200px; height: 960px; overflow: hidden;
    background: var(--page-bg);
    font-family: "Roboto", Arial, sans-serif;
  }
  .canvas { position: relative; width: 1200px; height: 960px; }
  .card {
    position: absolute; left: 215px; width: 702px; height: 401px; overflow: hidden;
  }
  .card--front { top: 60px; background: var(--brand-green); }
  .card--back { top: 500px; background: var(--card-dark); }

  /* front */
  .front-brand {
    position: absolute; left: 0; right: 0; top: 78px;
    display: flex; flex-direction: column; align-items: center;
  }
  .brand-dot {
    width: 150px; height: 150px; border-radius: 50%;
    background: var(--brand-green-deep);
  }
  .front-brand .brand-name {
    margin-top: 18px; font-size: 25px; font-weight: 700; letter-spacing: 2px;
    color: var(--brand-green-deep);
  }
  .front-brand .brand-phone {
    margin-top: 8px; font-size: 13px; font-weight: 700; letter-spacing: 9px;
    color: var(--brand-green-deep);
  }
  .tagline {
    position: absolute; left: 0; right: 0; top: 356px; text-align: center;
    font-size: 15.5px; letter-spacing: 0.6px; color: var(--text-light);
  }

  /* back */
  .back-watermark {
    position: absolute; left: -2px; top: 52px; width: 360px; height: 360px;
    border-radius: 50%; background: var(--card-dark-tone);
  }
  .back-brand {
    position: absolute; right: 30px; top: 28px; width: 190px;
    display: flex; flex-direction: column; align-items: center;
  }
  .back-brand .brand-dot { width: 96px; height: 96px; background: var(--brand-green); }
  .back-brand .brand-name {
    margin-top: 12px; font-size: 12.5px; font-weight: 700; letter-spacing: 1px;
    color: var(--brand-green); text-align: center; white-space: nowrap;
  }
  .back-brand .brand-phone {
    margin-top: 6px; font-size: 9px; font-weight: 700; letter-spacing: 6px;
    color: var(--brand-green);
  }
  .person-name {
    position: absolute; right: 30px; top: 230px;
    font-size: 34px; letter-spacing: 0.5px; color: var(--brand-green); white-space: nowrap;
  }
  .person-name .first { font-weight: 700; }
  .person-name .last { font-weight: 400; }
  .name-bar {
    position: absolute; right: 0; top: 233px; width: 19px; height: 31px;
    background: var(--brand-green);
  }
  .contact-list {
    position: absolute; right: 26px; top: 314px; list-style: none;
    display: flex; flex-direction: column; gap: 5px; align-items: flex-end;
  }
  .contact-item {
    display: flex; align-items: center; gap: 9px;
    font-size: 14.5px; letter-spacing: 0.5px; color: var(--text-light);
  }
  .contact-item svg { width: 15px; height: 15px; flex: none; }
</style>
</head>
<body>
<main class="canvas">
  <section class="card card--front" aria-label="Card front">
    <div class="front-brand">
      <div class="brand-dot"></div>
      <p class="brand-name">TRAVERSE GROUNDMAKRZ LLC</p>
      <p class="brand-phone">555-714-9082</p>
    </div>
    <p class="tagline">SPEACIALIZES IN LAND CLEARING , MUCLHING AND EXCAVATION</p>
  </section>

  <section class="card card--back" aria-label="Card back">
    <div class="back-watermark"></div>
    <div class="back-brand">
      <div class="brand-dot"></div>
      <p class="brand-name">TRAVERSE GROUNDMAKRZ LLC</p>
      <p class="brand-phone">555-714-9082</p>
    </div>
    <h1 class="person-name"><span class="first">DALE</span> <span class="last">VORSKIN</span></h1>
    <div class="name-bar"></div>
    <ul class="contact-list">
      <li class="contact-item">555- 714-9082
        <svg viewBox="0 0 24 24" aria-hidden="true"><path fill="var(--brand-green)" d="M6.6 10.8a15 15 0 0 0 6.6 6.6l2.2-2.2a1 1 0 0 1 1-.25 11.4 11.4 0 0 0 3.6.57 1 1 0 0 1 1 1V20a1 1 0 0 1-1 1A17 17 0 0 1 3 4a1 1 0 0 1 1-1h3.5a1 1 0 0 1 1 1c0 1.25.2 2.45.57 3.57a1 1 0 0 1-.25 1z"/></svg>
      </li>
      <li class="contact-item">WWW.TRV-GROUNDMAKRZ.COM
        <svg viewBox="0 0 24 24" aria-hidden="true"><circle cx="12" cy="12" r="10" fill="none" stroke="var(--brand-green)" stroke-width="2"/><path d="M2 12h20M12 2c3 3 3 17 0 20M12 2c-3 3-3 17 0 20" fill="none" stroke="var(--brand-green)" stroke-width="1.6"/></svg>
      </li>
      <li class="contact-item">OFFICE@TRV-GROUNDMAKRZ.COM
        <svg viewBox="0 0 24 24" aria-hidden="true"><rect x="2" y="6" width="20" height="14" rx="1" fill="none" stroke="var(--brand-green)" stroke-width="2"/><path d="M2 7l10 7 10-7" fill="none" stroke="var(--brand-green)" stroke-width="2"/></svg>
      </li>
    </ul>
  </section>
</main>
</body>
</html>
```